SaaS Early tech startup business card design

Unique design for experience ecommerce platform company. the business cards will be used by executive members. conformance with color code is required.

```html
<!DOCTYPE html>
<html lang="en">
<head>
<meta charset="utf-8">
<title>novra – business card</title>
<link href="https://fonts.googleapis.com/css2?family=Roboto:wght@400;700&display=swap" rel="stylesheet">
<style>
  :root {
    --backdrop: #6c6969;
    --teal-light: #15a393;
    --teal-dark: #0f666c;
    --brand-teal: #1a9c8f;
    --name-teal: #156f73;
    --paper: #f4f4f3;
    --ink: #2c2c2c;
    --white: #ffffff;
  }
  * { margin: 0; padding: 0; box-sizing: border-box; }
  html, body {
    width: 1200px; height: 1200px; overflow: hidden;
    background: var(--backdrop);
    font-family: "Roboto", Arial, sans-serif;
  }
  .canvas { position: relative; width: 1200px; height: 1200px; }

  .card {
    position: absolute;
    width: 593px; height: 348px;
    border-radius: 22px;
    overflow: hidden;
  }
  .card--front {
    left: 298px; top: 198px;
    background: linear-gradient(135deg, var(--teal-light) 0%, #12857f 55%, var(--teal-dark) 100%);
  }
  .card--back { left: 298px; top: 637px; background: var(--paper); }

  .front-brand {
    position: absolute; left: 0; right: 0; top: 122px;
    text-align: center; color: var(--white);
  }
  .front-brand__name {
    font-weight: 700; font-size: 92px; line-height: 1;
    letter-spacing: -1px;
  }
  .front-brand__tagline {
    margin-top: 10px;
    font-weight: 400; font-size: 16px; letter-spacing: 5px;
    padding-left: 5px;
  }

  .back-brand {
    position: absolute; left: 0; right: 0; top: 54px;
    text-align: center;
    font-weight: 700; font-size: 88px; line-height: 1;
    color: var(--brand-teal); letter-spacing: -1px;
  }
  .holder {
    position: absolute; left: 0; right: 0; top: 184px; text-align: center;
  }
  .holder__name { font-weight: 700; font-size: 24px; color: var(--name-teal); }
  .holder__role { margin-top: 2px; font-size: 16px; color: var(--ink); }

  .contact {
    position: absolute; left: 0; right: 0; top: 260px;
    font-size: 16px; color: var(--ink);
  }
  .contact__row {
    display: flex; justify-content: center; align-items: center;
    gap: 14px; height: 22px;
  }
  .contact__row--second { margin-top: 4px; }
  .contact__item { display: flex; align-items: center; gap: 10px; }
  .contact__icon { width: 14px; height: 14px; fill: var(--name-teal); }

  .back-band {
    position: absolute; left: 0; right: 0; bottom: 0; height: 9px;
    background: var(--brand-teal);
  }
</style>
</head>
<body>
<div class="canvas">

  <section class="card card--front">
    <div class="front-brand">
      <div class="front-brand__name">novra</div>
      <div class="front-brand__tagline">BUILT AROUND YOU</div>
    </div>
  </section>

  <section class="card card--back">
    <div class="back-brand">novra</div>
    <div class="holder">
      <div class="holder__name">Karim D.</div>
      <div class="holder__role">CTO/Owner</div>
    </div>
    <div class="contact">
      <div class="contact__row">
        <span class="contact__item">
          <svg class="contact__icon" viewBox="0 0 16 16" aria-hidden="true"><path d="M2 6 C2 3 14 3 14 6 L11 7 L10 5 L6 5 L5 7 Z M4 8 L12 8 L14 14 L2 14 Z"/></svg>
          (00) 0111 NOVR
        </span>
        <span class="contact__item">
          <svg class="contact__icon" viewBox="0 0 16 16" aria-hidden="true"><path d="M1 3 L15 3 L15 13 L1 13 Z M2 4 L8 9 L14 4 Z" fill-rule="evenodd"/></svg>
          info@novra.net
        </span>
        <span class="contact__item">
          <svg class="contact__icon" viewBox="0 0 16 16" aria-hidden="true"><circle cx="8" cy="8" r="7" fill="none" stroke="var(--name-teal)" stroke-width="1.6"/><path d="M1 8 H15 M8 1 C4 5 4 11 8 15 M8 1 C12 5 12 11 8 15" fill="none" stroke="var(--name-teal)" stroke-width="1.3"/></svg>
          www.novra.net
        </span>
      </div>
      <div class="contact__row contact__row--second">
        <span class="contact__item">
          <svg class="contact__icon" viewBox="0 0 16 16" aria-hidden="true"><path d="M8 1 C4.7 1 3 3.4 3 6 C3 9.5 8 15 8 15 C8 15 13 9.5 13 6 C13 3.4 11.3 1 8 1 Z M8 4 A2 2 0 1 1 8 8 A2 2 0 1 1 8 4 Z" fill-rule="evenodd"/></svg>
          Harbor Tower, Dubai, Media District, UAE
        </span>
      </div>
    </div>
    <div class="back-band"></div>
  </section>

</div>
</body>
</html>
```